Web Site Design For Real Estate Sales Project

The idea behind this project is pretty simple. I am putting my penthouse apartment up for sale and am trying to be creative in selling it.
Technically this will be pretty simple, it will be 3 pages but graphically this has to be as impressive as possible which is why I am trying Pixel Harbor.
The apartment is located in Barra Da Tijuca, Rio De Janeiro, Brazil. (This is where the 2016 Solstice Meet will be held)
I am looking for an index page and 2 sub-pages. I am open to all kinds of designs and navigation's but it has to make an impression quickly with a professional and enticing design. The index page should make it obvious that there is a penthouse apartment for sale in Barra Da Tijuca ( suburb of Rio De Janeiro). The first sub page is about the Condominium where the apartment is located, the second sub page is about the apartment itself.
Here is a more detailed description of what the 3 pages should be about.
Index Page
This is the landing page and should make it obvious that there is an apartment for sale in Barra Da Tijuca, Rio De Janeiro with the following attributes
251 SQ M
Duplex Penthouse
4 suites
Price R$ 2.200.000
Price per SQ M: R$ 8.764
First Sub-Page
This is about the Condominium which is called "Tranquil Cliff Suites" with the following bullets
*Family friendly and safe
*Direct access to the beach
*Many amenities like pool, football court, gym, sauna
There should be some photos of the condominium and a link to the site of the condominium ( www.tcsqv.com )
Second Sub-page
This is about the apartment. It should list in bullets the features of the apartment and then have a photo gallery of the view and various rooms. I have attached sample photos but will eventually have to use more photos.
Apartment Features
Price: R$ 2.220.000
251 m2 Duplex Penthouse
4 suites
maids room with bath
guest bathroom
living room
dinning room
Terrace with heated pool for year round use
Veranda
As mentioned above I am open to all designs and navigation so feel free to be creative. The important thing is catch peoples attention and get the message across in a few seconds, which is that there is an apartment for sale at this price with these features in this location. I will then use zintra clickreach and SEO to get people to the site.
Thanks
Men and Women from 30-60 years of age.
Apartment

```html
<!DOCTYPE html>
<html lang="en">
<head>
<meta charset="utf-8">
<title>Penthouse Sale – Barra da Tijuca</title>
<link href="https://fonts.googleapis.com/css2?family=Jost:wght@400;500;600&family=Noto+Sans:wght@400&display=swap" rel="stylesheet">
<style>
:root{
  --blue:#1a8ee0;
  --blue-dark:#0b6cc0;
  --nav-a:#2b96ea;
  --nav-b:#0a68bd;
  --text:#555;
  --text-soft:#777;
  --orange-a:#f9bd52;
  --orange-b:#ee8e1e;
  --lime:#c9f26b;
  --sky:#6ea9d8;
  --sea:#2b78b6;
  --green-a:#86a84a;
  --green-b:#5e8132;
  --bg:#e6e6e6;
  --footer:#7d7d7d;
  --white:#fff;
}
*{margin:0;padding:0;box-sizing:border-box}
html,body{width:1113px;height:1200px;overflow:hidden}
body{position:relative;background:var(--bg);font-family:"Noto Sans",Verdana,sans-serif;color:var(--text)}
.abs{position:absolute}

.intro{left:0;top:0;width:348px;height:394px;background:var(--white)}
.intro h1{position:absolute;left:139px;top:48px;font-family:"Jost",sans-serif;font-weight:600;font-size:23px;color:var(--blue);letter-spacing:.2px}
.features{position:absolute;left:139px;top:108px;list-style:none;font-size:11.3px;color:#666;line-height:21px}
.features li{position:relative;padding-left:18px;margin-bottom:17px}
.features li::before{content:"";position:absolute;left:0;top:9px;width:3px;height:3px;border-radius:50%;background:var(--blue)}

.hero-sky{left:348px;top:0;width:765px;height:394px;background:linear-gradient(180deg,var(--sky) 0%,#dfe9ef 40%,var(--sea) 62%,#8fa58a 100%)}
.hero-green{left:348px;top:394px;width:765px;height:181px;background:linear-gradient(135deg,var(--green-a),var(--green-b))}

.nav{left:556px;top:42px;width:557px;height:54px;background:linear-gradient(90deg,var(--nav-a),var(--nav-b));display:flex;align-items:center;padding-left:33px;gap:37px}
.nav a{color:var(--white);text-decoration:none;font-family:"Jost",sans-serif;font-size:13px;letter-spacing:.2px}

.specs{left:0;top:394px;width:348px;height:181px;background:linear-gradient(90deg,var(--orange-a),var(--orange-b));padding:31px 0 0 138px;color:var(--white);font-family:"Jost",sans-serif;font-size:16.5px;line-height:26px}
.specs b{font-weight:600}

.headline{right:139px;top:432px;text-align:right;font-family:"Jost",sans-serif;font-weight:600;font-size:26px;line-height:41px;color:var(--lime);text-transform:uppercase}
.dots{left:889px;top:537px;display:flex;gap:10px}
.dots span{width:14px;height:14px;border-radius:50%;background:#eee}
.dots span.on{background:#8fd12b}

.gallery{left:139px;top:594px;width:835px;height:171px;background:var(--white);box-shadow:0 1px 3px rgba(0,0,0,.12)}
.gallery h2{position:absolute;left:20px;top:15px;font-family:"Jost",sans-serif;font-weight:400;font-size:17px;color:var(--blue-dark)}
.thumb{position:absolute;top:54px;width:147px;height:94px}
.t1{background:linear-gradient(135deg,#d8d4cc,#6b4a36)}
.t2{background:linear-gradient(180deg,#b8c6cf,#e3e3e1 60%,#6a3a25)}
.t3{background:linear-gradient(180deg,#9fb7cc,#7a8b6a 60%,#3d3a2c)}
.t4{background:linear-gradient(135deg,#a9bfd1,#b5856d 50%,#3c2a20)}
.t5{background:linear-gradient(135deg,#e8e1d4,#7a5a42 60%,#2f2a28)}

.suite-title{left:139px;top:795px;font-family:"Jost",sans-serif;font-weight:400;font-size:17px;color:var(--blue-dark)}
.arrows{left:937px;top:806px}
.copy{left:139px;top:855px;width:310px;font-size:11.3px;color:var(--text-soft);line-height:21px}
.copy p{margin-bottom:10px}
.feature-photo{left:486px;top:858px;width:261px;height:174px;background:linear-gradient(180deg,#a8bed0 0%,#c9b29c 35%,#e5e5e2 65%,#8a8a88 100%)}
.details{left:772px;top:855px;width:200px;font-family:"Jost",sans-serif}
.details h3{font-weight:400;font-size:13.5px;color:#333;margin-bottom:4px}
.details p{font-size:10.5px;color:#666;line-height:22.5px;margin-bottom:6px}

.footer-band{left:0;top:1130px;width:1113px;height:19px;background:#f2f2f2}
.footer{left:0;top:1149px;width:1113px;height:51px;background:linear-gradient(180deg,#6e6e6e,var(--footer));color:var(--white);font-family:"Jost",sans-serif;font-size:11px}
.footer .copyright{position:absolute;left:139px;top:21px}
.footer .legal{position:absolute;left:463px;top:20px;color:#ddd}
.footer .legal span{margin:0 9px}
.footer .social{position:absolute;left:822px;top:17px;display:flex;align-items:center;gap:7px;color:#eee}
.footer .social i{display:block;width:18px;height:18px;border-radius:50%;background:#d6d6d6}
.footer .social em{font-style:normal;margin-right:17px}
</style>
</head>
<body>

<section class="abs intro">
  <h1>PENTHOUSE SALE</h1>
  <ul class="features">
    <li>Maids room with bath</li>
    <li>Guest bathroom</li>
    <li>Living room</li>
    <li>Dinning room</li>
    <li>Terrace with heated pool<br>for year Round use</li>
    <li>Veranda</li>
  </ul>
</section>

<div class="abs hero-sky" role="img" aria-label="Aerial view of the Barra da Tijuca coastline, beach and high-rise buildings"></div>
<div class="abs hero-green" role="img" aria-label="Green aerial view of lagoons and vegetation around Barra da Tijuca"></div>

<nav class="abs nav">
  <a href="#">Home</a>
  <a href="#">Tranquil Cliff Suites</a>
  <a href="#">The Apartment</a>
</nav>

<section class="abs specs">
  251 SQ M<br>
  <b>Duplex Penthouse</b><br>
  4 suites<br>
  <b>PRICE R$ 2.200.000</b><br>
  Price per SQ M: R$ 8.764
</section>

<p class="abs headline">My penthouse which is located at<br>Barra da Tijuca</p>
<div class="abs dots"><span></span><span></span><span></span><span class="on"></span></div>

<section class="abs gallery">
  <h2>Penthouse Suite</h2>
  <div class="thumb t1" style="left:24px" role="img" aria-label="Living room interior"></div>
  <div class="thumb t2" style="left:184px" role="img" aria-label="Terrace with barbecue"></div>
  <div class="thumb t3" style="left:344px" role="img" aria-label="View of the mountains from the terrace"></div>
  <div class="thumb t4" style="left:505px" role="img" aria-label="Terrace barbecue corner"></div>
  <div class="thumb t5" style="left:664px" role="img" aria-label="Interior staircase and lounge"></div>
</section>

<h2 class="abs suite-title">Tranquil Cliff Suite</h2>
<svg class="abs arrows" width="30" height="16" viewBox="0 0 30 16" aria-hidden="true">
  <polyline points="9,2 3,8 9,14" fill="none" stroke="#888" stroke-width="1.5"/>
  <polyline points="21,2 27,8 21,14" fill="none" stroke="#888" stroke-width="1.5"/>
</svg>

<div class="abs copy">
  <p>Lorem ipsum dolor sit amet, consectetur adipiscing elit.</p>
  <p>Phasellus ultrices sapien iaculis neque volutpat ut vulputate urna viverra.</p>
  <p>Proin et tortor et enim volutpat fringilla sit amet at arcu.</p>
  <p>Nunc dignissim ultricies felis, nec malesuada nisi suscipit vitae.</p>
  <p>Duis sit amet tortor enim, a ultricies dolor.</p>
</div>

<div class="abs feature-photo" role="img" aria-label="Rooftop terrace with barbecue and mountain view"></div>

<div class="abs details">
  <h3>Description</h3>
  <p>House, 251 sqn<br>4 Suites<br>5 Bathrooms,</p>
  <h3>Facilities</h3>
  <p>archipelago, swimming pool,<br>big private garden, saunas, high<br>standard of interior, private beach</p>
</div>

<div class="abs footer-band"></div>
<footer class="abs footer">
  <span class="copyright">Copyright © 2013. All Rights Reserved</span>
  <span class="legal">Terms &amp; Condition<span>|</span>Privacy Policy</span>
  <span class="social"><em>Social Media</em><i></i><i></i><i></i></span>
</footer>

</body>
</html>
```